Calloway Metal Recyclers - www.callowayrecyclers-example.com.au

I've just rebranded my business and thought what better way to continue with this than getting a website.
It is going to be fairly basic for now. I've attached quite a few images, feel free to use whichever you like.
And pages description is also attached in a .doc file.
Updates

Hi, this is my first time having a website. I am open to anything and trust the experience and ideas you can bring forward. I will look at extending the deadline so I can take my time to give feedback as needed! Thank you all.

Target Market(s)

Mining and industrial and commercial sectors

Coding

Coded - Design and coding required

Number of Pages Required

5+ page

Requirements
Must have
• Logo/Phone number at the top of every page. "Scrap Metal Specialists" tag line at the top of every page.
Nice to have
• Top Navigation.

```html
<!DOCTYPE html>
<html lang="en">
<head>
<meta charset="utf-8">
<title>Calloway Metal Recyclers</title>
<link href="https://fonts.googleapis.com/css2?family=Bebas+Neue&family=Roboto:wght@300;400;500;700&display=swap" rel="stylesheet">
<style>
:root{
  --navy:#163668;
  --navy-dark:#0f2548;
  --grey-bar:#6f6f6f;
  --text:#5b5b5b;
  --heading-grey:#666;
  --white:#fff;
  --field:#fff;
  --shadow:0 4px 18px rgba(0,0,0,.12);
}
*{box-sizing:border-box;margin:0;padding:0}
html,body{width:1200px;height:2919px;overflow:hidden}
body{font-family:"Roboto",sans-serif;color:var(--text);background:var(--white)}
.page{position:relative;width:1200px;height:2919px;overflow:hidden}
.abs{position:absolute}
.display{font-family:"Bebas Neue",sans-serif;letter-spacing:.5px;font-weight:400}

/* top bar */
.topbar{left:0;top:0;width:1200px;height:48px;background:var(--navy);color:#fff;font-size:14px}
.topbar-left{left:0;top:0;height:48px;width:490px;background:var(--grey-bar);clip-path:polygon(0 0,100% 0,450px 100%,0 100%)}
.topbar-left span{position:absolute;left:111px;top:15px}
.topbar-tagline{left:520px;top:15px;width:250px;text-align:center;font-weight:500;letter-spacing:1px;text-transform:uppercase;font-size:13px}
.topbar-call{left:796px;top:15px}
.social{display:flex;gap:6px}
.social i{display:block;width:34px;height:34px;border-radius:50%;border:1.5px solid #fff}
.social i.filled{background:#fff}
.topbar .social{position:absolute;left:977px;top:7px}

/* hero */
.hero{left:0;top:48px;width:1200px;height:737px;background:radial-gradient(ellipse at 75% 40%,#6b5a3a 0%,#3a3326 40%,#1c1f26 75%),#222}
.nav{top:92px;font-size:15px;font-weight:500;color:#fff;display:flex;gap:38px}
.nav-left{left:111px}
.nav-right{left:805px;gap:35px}
.nav .active{border-bottom:2px solid #fff;padding-bottom:8px}
.logo{color:#fff;text-align:center;font-family:"Bebas Neue",sans-serif;line-height:.95}
.logo .name{font-size:34px}
.logo .sub{font-size:19px}
.logo .phone{font-family:"Roboto",sans-serif;font-size:13px;font-weight:700;margin-top:3px}
.hero-logo{left:500px;top:72px;width:200px}
.hero-welcome{left:111px;top:244px;color:#fff;font-size:28px}
.hero-title{left:111px;top:276px;color:#fff;font-size:51px;white-space:nowrap}
.hero-text{left:111px;top:342px;width:460px;color:#fff;font-size:18px;line-height:28px}
.btn{display:block;background:var(--navy);color:#fff;font-weight:500;text-align:center;border-radius:3px;font-size:15px}
.hero-btn{left:111px;top:424px;width:151px;height:51px;line-height:51px}
.dots{left:1137px;top:342px;display:flex;flex-direction:column;gap:19px}
.dots i{width:9px;height:9px;border:1.5px solid #fff;transform:rotate(45deg)}
.dots i.on{background:#fff}

/* about */
.about-frame{left:111px;top:965px;width:356px;height:318px;border:10px solid var(--navy);border-top:none}
.about-frame:before{content:"";position:absolute;left:-10px;top:0;width:68px;height:10px;background:var(--navy)}
.photo{background:linear-gradient(160deg,#6f8aa3 0%,#8a5a3a 45%,#6a4a34 100%)}
.about-img1{left:187px;top:805px;width:298px;height:333px}
.about-img2{left:343px;top:968px;width:237px;height:261px;border:8px solid #fff;background-clip:padding-box;background-image:linear-gradient(170deg,#a9bfd4 0%,#9b4a2c 45%,#b0674a 100%)}
.about-label{left:638px;top:882px;color:var(--navy);font-size:40px}
.about-title{left:638px;top:927px;color:var(--heading-grey);font-size:42px;white-space:nowrap}
.about-text{left:638px;top:996px;width:451px;font-size:14px;font-weight:300;line-height:26.5px;text-align:justify}
.about-btn{left:638px;top:1138px;width:143px;height:51px;line-height:51px}

/* services */
.services-band{left:0;top:1401px;width:1200px;height:366px;background:linear-gradient(180deg,#14284c,#1a3563)}
.services-title{left:0;top:1474px;width:1200px;text-align:center;color:#fff;font-size:54px}
.arrow{width:38px;height:38px;border-radius:50%;border:1.5px solid #fff;display:flex;align-items:center;justify-content:center}
.arrow.next{background:#fff}
.card{top:1583px;width:309px;height:368px;background:#fff;box-shadow:var(--shadow)}
.card .pic{position:absolute;left:7px;top:7px;width:295px;height:235px}
.card .icon{position:absolute;left:104px;top:192px;width:102px;height:102px;border-radius:50%;background:var(--navy);border:7px solid #c9ccd2;display:flex;align-items:center;justify-content:center}
.card .icon.muted{background:#8a8a8a}
.card .label{position:absolute;left:0;width:309px;text-align:center;font-size:19px;font-weight:500;line-height:26px;color:#777}
.card .label.hl{color:var(--navy)}

/* contact */
.touch-title{left:0;top:2052px;width:1200px;text-align:center;font-size:64px;color:var(--navy)}
.touch-title span{color:var(--heading-grey)}
.c-icon{left:133px;width:80px;height:80px;border-radius:50%;background:#fff;box-shadow:var(--shadow);display:flex;align-items:center;justify-content:center}
.c-label{left:240px;font-size:14px;font-weight:700;color:#333}
.c-value{left:240px;width:220px;font-size:14px;line-height:20px;color:#777;overflow-wrap:anywhere}
.field{background:var(--field);box-shadow:0 2px 12px rgba(0,0,0,.09);font-size:14px;color:#777;padding:16px 17px}
.send{left:490px;top:2418px;width:197px;height:51px;line-height:51px;font-size:16px}

/* footer */
.footer{left:0;top:2567px;width:1200px;height:352px;background:var(--navy)}
.footer-logo{left:500px;top:2610px;width:200px}
.footer-nav{left:0;top:2727px;width:1200px;display:flex;justify-content:center;gap:22px;color:#fff;font-size:17px;font-weight:500}
.footer-contact{left:0;top:2761px;width:1200px;display:flex;justify-content:center;align-items:center;gap:22px;color:#fff;font-size:17px;font-weight:500}
.footer-contact span{display:flex;align-items:center;gap:12px}
.footer-rule{left:111px;top:2856px;width:978px;height:1px;background:rgba(255,255,255,.35)}
.copyright{left:0;top:2879px;width:1200px;text-align:center;color:#fff;font-size:12px}
</style>
</head>
<body>
<div class="page">

  <!-- hero -->
  <div class="abs hero" role="img" aria-label="Scrap yard with large cable drums and metal scrap at dusk"></div>
  <svg class="abs" style="left:0;top:540px" width="1200" height="250" viewBox="0 0 1200 250">
    <polygon points="0,245 400,10 1200,245" fill="#163668"/>
    <polygon points="120,245 400,38 1200,245" fill="#ffffff"/>
    <polyline points="235,110 400,28 720,120" fill="none" stroke="#ffffff" stroke-width="5"/>
    <rect x="0" y="245" width="1200" height="5" fill="#fff"/>
  </svg>

  <div class="abs topbar">
    <div class="abs topbar-left"><span>Email Us : dan@callowayrecyclers-example.com.au</span></div>
    <span class="abs topbar-tagline">Scrap Metal Specialists</span>
    <span class="abs topbar-call">Call Us : 0491570156</span>
    <div class="social"><i class="filled"></i><i></i><i></i></div>
  </div>

  <nav class="abs nav nav-left"><span class="active">HOME</span><span>ABOUT</span><span>SERVICES &#8964;</span></nav>
  <nav class="abs nav nav-right"><span>ONLINE STORE</span><span>BLOG</span><span>CONTACT</span></nav>
  <div class="abs logo hero-logo"><div class="name">CALLOWAY</div><div class="name" style="font-size:19px">METAL RECYCLERS</div><div class="phone">0491570156</div></div>

  <div class="abs display hero-welcome">WELCOME TO</div>
  <h1 class="abs display hero-title">CALLOWAY METAL RECYCLERS</h1>
  <p class="abs hero-text">We are a Perth based company that provides scrap metal collection and oxy cutting services</p>
  <span class="abs btn hero-btn">GET STARTED</span>
  <div class="abs dots"><i></i><i class="on"></i><i></i><i></i></div>

  <!-- about -->
  <div class="abs about-frame"></div>
  <div class="abs photo about-img1" role="img" aria-label="Rusted steel bin in a yard under trees"></div>
  <div class="abs about-img2" role="img" aria-label="Large rusted steel structure on red dirt"></div>
  <div class="abs display about-label">ABOUT</div>
  <h2 class="abs display about-title">CALLOWAY METAL RECYCLERS</h2>
  <p class="abs about-text">My name is Dan Calloway and I'm the managing director of Calloway Metal Processors. I have been in the scrap metal recycling industry longer than I haven't! I have 16 years' experience in everything scrap metal and I am very passionate about sustainable recycling.</p>
  <span class="abs btn about-btn">LEARN MORE</span>

  <!-- services -->
  <div class="abs services-band"></div>
  <h2 class="abs display services-title">OUR SERVICES</h2>
  <div class="abs arrow" style="left:1006px;top:1486px"><svg width="12" height="14" viewBox="0 0 12 14"><path d="M8 1 2 7l6 6" fill="none" stroke="#fff" stroke-width="2"/></svg></div>
  <div class="abs arrow next" style="left:1050px;top:1486px"><svg width="12" height="14" viewBox="0 0 12 14"><path d="M4 1l6 6-6 6" fill="none" stroke="#163668" stroke-width="2"/></svg></div>

  <div class="abs card" style="left:111px">
    <div class="pic" role="img" aria-label="Metal drum being cut with oxy torch" style="background:linear-gradient(150deg,#3b3a36,#6d8f86 60%,#2b2a28)"></div>
    <div class="icon"><svg width="40" height="40" viewBox="0 0 40 40" fill="none" stroke="#fff" stroke-width="2"><path d="M6 6h28M14 6v10h12V6M17 16v10h6V16M20 26v8M12 36h16"/></svg></div>
    <div class="label" style="top:312px">OXY CUTTING</div>
  </div>
  <div class="abs card" style="left:445px">
    <div class="pic" role="img" aria-label="Yellow heavy industrial machinery parts" style="background:linear-gradient(150deg,#6b6a64,#b58a2a 55%,#4a4840)"></div>
    <div class="icon muted"><svg width="40" height="40" viewBox="0 0 40 40" fill="none" stroke="#fff" stroke-width="2"><path d="M5 34h30M8 34V18l8 5v-5l8 5V10h8v24M12 28h3M20 28h3M28 28h3"/></svg></div>
    <div class="label hl" style="top:298px">HEAVY INDUSTRIAL<br>EQUIPMENT</div>
  </div>
  <div class="abs card" style="left:780px">
    <div class="pic" role="img" aria-label="Curved steel sections laid out on dirt" style="background:linear-gradient(160deg,#4a4744,#8a7a68 55%,#6b5a48)"></div>
    <div class="icon"><svg width="40" height="40" viewBox="0 0 40 40" fill="none" stroke="#fff" stroke-width="2"><circle cx="20" cy="20" r="14"/><circle cx="20" cy="20" r="9"/><circle cx="20" cy="20" r="4"/></svg></div>
    <div class="label" style="top:298px">TRANSPORT AND<br>COLLECTION</div>
  </div>

  <!-- contact -->
  <h2 class="abs display touch-title">GET <span>IN TOUCH</span></h2>

  <div class="abs c-icon" style="top:2165px"><svg width="36" height="36" viewBox="0 0 36 36" fill="none" stroke="#163668" stroke-width="2.5"><path d="M18 30s-9-9-9-16a9 9 0 0 1 18 0c0 7-9 16-9 16z"/><circle cx="18" cy="14" r="3"/><ellipse cx="18" cy="31" rx="12" ry="3"/></svg></div>
  <div class="abs c-label" style="top:2173px">LOCATION:</div>
  <div class="abs c-value" style="top:2199px">Dan Calloway,<br>WA, United States</div>

  <div class="abs c-icon" style="top:2268px"><svg width="36" height="36" viewBox="0 0 24 24" fill="#163668"><path d="M6.6 10.8a15 15 0 0 0 6.6 6.6l2.2-2.2c.3-.3.7-.4 1-.2 1.1.4 2.3.6 3.6.6.6 0 1 .4 1 1V20c0 .6-.4 1-1 1A17 17 0 0 1 3 4c0-.6.4-1 1-1h3.5c.6 0 1 .4 1 1 0 1.2.2 2.4.6 3.6.1.3 0 .7-.2 1z"/></svg></div>
  <div class="abs c-label" style="top:2279px">PHONE:</div>
  <div class="abs c-value" style="top:2311px">0491570156</div>

  <div class="abs c-icon" style="top:2370px"><svg width="36" height="28" viewBox="0 0 36 28"><rect width="36" height="28" rx="3" fill="#163668"/><path d="M2 3l16 13L34 3" fill="none" stroke="#fff" stroke-width="2.5"/></svg></div>
  <div class="abs c-label" style="top:2381px">EMAIL:</div>
  <div class="abs c-value" style="top:2413px">dan@callowayrecyclers-<br>example.com.au</div>

  <div class="abs field" style="left:490px;top:2165px;width:283px;height:49px">First Name</div>
  <div class="abs field" style="left:784px;top:2165px;width:283px;height:49px">Last Name</div>
  <div class="abs field" style="left:490px;top:2228px;width:283px;height:49px">Email Address</div>
  <div class="abs field" style="left:784px;top:2228px;width:283px;height:49px">Phone Number</div>
  <div class="abs field" style="left:490px;top:2292px;width:577px;height:111px">Message</div>
  <span class="abs btn send">SEND MESSAGE</span>

  <!-- footer -->
  <div class="abs footer"></div>
  <div class="abs logo footer-logo"><div class="name">CALLOWAY</div><div class="name" style="font-size:19px">METAL RECYCLERS</div><div class="phone">0491570156</div></div>
  <nav class="abs footer-nav"><span>HOME</span><span>|</span><span>ABOUT</span><span>|</span><span>SERVICES</span><span>|</span><span>ONLINE STORE</span><span>|</span><span>BLOG</span><span>|</span><span>CONTACT</span></nav>
  <div class="abs footer-contact">
    <span><svg width="15" height="15" viewBox="0 0 24 24" fill="#fff"><path d="M6.6 10.8a15 15 0 0 0 6.6 6.6l2.2-2.2c.3-.3.7-.4 1-.2 1.1.4 2.3.6 3.6.6.6 0 1 .4 1 1V20c0 .6-.4 1-1 1A17 17 0 0 1 3 4c0-.6.4-1 1-1h3.5c.6 0 1 .4 1 1 0 1.2.2 2.4.6 3.6.1.3 0 .7-.2 1z"/></svg>0491570156</span>
    <span>|</span>
    <span><svg width="18" height="14" viewBox="0 0 36 28"><rect width="36" height="28" rx="3" fill="#fff"/><path d="M2 3l16 13L34 3" fill="none" stroke="#163668" stroke-width="3"/></svg>dan@callowayrecyclers-example.com.au</span>
  </div>
  <div class="abs social" style="left:543px;top:2800px"><i class="filled"></i><i></i><i></i></div>
  <div class="abs footer-rule"></div>
  <div class="abs copyright">&copy; 2022 <b>CALLOWAY METAL RECYCLERS</b> &nbsp;|&nbsp; All Rights Reserved</div>

</div>
</body>
</html>
```